Custom Woodworking and Rock Design

We specialize in original, high quality, wood and rock art. It’s should be self explanatory ask questions if you need. Your team designing a logo. Furniture is custom made to order. Rocks are designed depending on consumer needs. Wood and rock can also be combined for custom work. Painted rocks on vintage wood. Custom chairs and cabinets. Artistic rocks for multiple uses:garden, magnets, custom. All ideas and requests are welcome.

Target Market(s)

All

Contact Information for Business Card

Mara Voss
Talbertstonecraft@mailbrook.net

Font styles to use
Sans Serif

Requirements
Must have
• Clear lettering
Nice to have
• Eye catching
Should not have
• Blurr

```html
<!DOCTYPE html>
<html lang="en">
<head>
<meta charset="utf-8">
<title>Talbert Stonecraft – Business Card</title>
<link rel="stylesheet" href="https://fonts.googleapis.com/css2?family=Open+Sans:wght@400;600;700&display=swap">
<style>
  :root{
    --stage:#2b2b2b;
    --card-dark:#3f3f41;
    --card-dark-2:#5a5a5c;
    --paper:#ffffff;
    --tab:#a9a9ab;
    --band:#b4b4b6;
    --band-2:#8f8f91;
    --ink-grey:#8a8a8c;
    --ink-light:#ffffff;
  }
  *{box-sizing:border-box;margin:0;padding:0}
  html,body{width:1200px;height:770px;overflow:hidden}
  body{background:var(--stage);font-family:"Open Sans",Arial,sans-serif;position:relative}

  .card{position:absolute;width:480px;height:272px;border-radius:18px;background:var(--card-dark);overflow:hidden;box-shadow:0 10px 24px rgba(0,0,0,.45)}
  .card--front{left:90px;top:110px}
  .card--back{left:630px;top:390px;background:linear-gradient(135deg,var(--card-dark-2),var(--card-dark))}

  /* front */
  .front-panel{position:absolute;left:0;right:0;top:20px;bottom:20px;background:var(--paper)}
  .edge-tab{position:absolute;width:16px;height:110px;background:var(--tab)}
  .edge-tab--left{left:14px;top:80px}
  .edge-tab--right{right:14px;top:20px}
  .brand{position:absolute;display:flex;flex-direction:column;align-items:center;justify-content:center;gap:12px}
  .card--front .brand{left:0;right:0;top:90px}
  .brand-mark{width:30px;height:30px;background:var(--ink-grey)}
  .brand-name{font-weight:700;font-size:26px;color:var(--ink-grey);letter-spacing:.5px;text-transform:uppercase;text-align:center;line-height:1.2}

  /* back */
  .back-panel{position:absolute;left:18px;top:0;bottom:0;width:200px;background:var(--paper)}
  .back-panel .tab{position:absolute;background:var(--tab);height:12px}
  .back-panel .tab--top{left:40px;width:110px;top:12px}
  .back-panel .tab--bottom{left:80px;width:120px;bottom:10px}
  .card--back .brand{left:18px;width:200px;top:118px;gap:10px}
  .card--back .brand-mark{width:26px;height:26px}
  .card--back .brand-name{font-size:17px;line-height:1.25}

  .band{position:absolute;left:218px;right:0;background:linear-gradient(90deg,var(--band),var(--band-2));color:var(--ink-light);padding-left:12px}
  .band--company{top:24px;height:30px;font-size:16px;font-weight:600;line-height:30px}
  .band--person{top:64px;height:48px;padding-top:4px}
  .person-name{font-size:16px;font-weight:600;text-transform:uppercase;letter-spacing:.5px;line-height:20px}
  .person-role{font-size:13px;font-weight:600;line-height:18px}
  .band--contact{top:122px;height:96px;padding-top:8px}
  .contact-row{display:flex;align-items:center;gap:8px;font-size:12.5px;line-height:19px;white-space:nowrap}
  .contact-row svg{width:16px;height:14px;flex:none}
  .contact-row .spacer{width:16px;flex:none}
</style>
</head>
<body>

<section class="card card--front" aria-label="Business card front">
  <div class="front-panel"></div>
  <div class="edge-tab edge-tab--left"></div>
  <div class="edge-tab edge-tab--right"></div>
  <div class="brand">
    <span class="brand-mark"></span>
    <span class="brand-name">Talbert Stonecraft</span>
  </div>
</section>

<section class="card card--back" aria-label="Business card back">
  <div class="back-panel">
    <div class="tab tab--top"></div>
    <div class="tab tab--bottom"></div>
  </div>
  <div class="brand">
    <span class="brand-mark"></span>
    <span class="brand-name">Talbert<br>Stonecraft</span>
  </div>

  <div class="band band--company">Talbert Stonecraft</div>
  <div class="band band--person">
    <p class="person-name">Mara Voss</p>
    <p class="person-role">Director</p>
  </div>
  <div class="band band--contact">
    <div class="contact-row">
      <svg viewBox="0 0 16 14"><path d="M2 4c0-2 12-2 12 0v1h-3V4H5v1H2z" fill="#fff"/><rect x="4" y="6" width="8" height="7" rx="1" fill="#fff"/></svg>
      <span>555-014-2388</span>
    </div>
    <div class="contact-row"><span class="spacer"></span><span>shop.mailbrook.net</span></div>
    <div class="contact-row">
      <svg viewBox="0 0 16 14"><rect x="1" y="2" width="14" height="10" fill="#fff"/><path d="M1 2l7 6 7-6" fill="none" stroke="#8f8f91" stroke-width="1.3"/></svg>
      <span>Talbertstonecraft@mailbrook.net</span>
    </div>
    <div class="contact-row">
      <svg viewBox="0 0 16 14"><rect x="1" y="1" width="14" height="9" rx="1" fill="#fff"/><rect x="6" y="10" width="4" height="2" fill="#fff"/><rect x="4" y="12" width="8" height="1.5" fill="#fff"/></svg>
      <span>www.talbert.mailbrook.net</span>
    </div>
  </div>
</section>

</body>
</html>
```